Vantiqo custom business card design

Need a authentic, innovative business card design for a new mobile app business. I am uploading a few screen images from our app for you to view. I would like app design theme to match business card design. I can also send logo images.

```html
<!DOCTYPE html>
<html lang="en">
<head>
<meta charset="UTF-8">
<title>Vantiqo Business Card</title>
<link href="https://fonts.googleapis.com/css2?family=Work+Sans:wght@400;500;800&display=swap" rel="stylesheet">
<style>
  :root {
    --backdrop: #161616;
    --card: #232323;
    --card-edge: #2c2c2c;
    --purple: #6b2f9e;
    --white: #ffffff;
    --muted: #d9d9d9;
  }
  * { box-sizing: border-box; margin: 0; padding: 0; }
  html, body {
    width: 1200px;
    height: 900px;
    overflow: hidden;
    background: var(--backdrop);
    font-family: "Work Sans", sans-serif;
  }
  .stage {
    position: relative;
    width: 1200px;
    height: 900px;
  }
  .card {
    position: absolute;
    left: 320px;
    width: 560px;
    height: 320px;
    background: var(--card);
    border: 1px solid var(--card-edge);
    box-shadow: 0 18px 40px rgba(0,0,0,0.55);
  }
  .card--front { top: 100px; }
  .card--back { top: 470px; }

  .brand {
    display: flex;
    flex-direction: column;
    align-items: center;
    gap: 14px;
  }
  .brand__dot {
    width: 84px;
    height: 84px;
    border-radius: 50%;
    background: var(--purple);
  }
  .brand__name {
    font-weight: 800;
    font-size: 38px;
    letter-spacing: 0.5px;
    color: var(--white);
    line-height: 1;
  }
  .card--front .brand {
    position: absolute;
    inset: 0;
    justify-content: center;
  }

  .card--back .brand {
    position: absolute;
    left: 40px;
    top: 0;
    bottom: 0;
    width: 210px;
    justify-content: center;
  }
  .card--back .brand__dot { width: 110px; height: 110px; }
  .card--back .brand__name { font-size: 42px; }

  .divider {
    position: absolute;
    left: 282px;
    top: 60px;
    width: 2px;
    height: 200px;
    background: var(--purple);
  }

  .contact {
    position: absolute;
    left: 318px;
    top: 52px;
    right: 20px;
    color: var(--white);
  }
  .contact__name {
    font-size: 22px;
    font-weight: 500;
    color: var(--purple);
    letter-spacing: 1px;
    text-transform: uppercase;
    line-height: 1;
  }
  .contact__role {
    font-size: 15px;
    color: var(--muted);
    margin-top: 4px;
  }
  .contact__address {
    font-size: 15px;
    line-height: 1.45;
    margin-top: 14px;
  }
  .contact__list {
    list-style: none;
    margin-top: 12px;
  }
  .contact__item {
    display: flex;
    align-items: center;
    gap: 10px;
    font-size: 15px;
    line-height: 1.65;
  }
  .contact__icon {
    width: 14px;
    height: 14px;
    flex: none;
  }
</style>
</head>
<body>
  <main class="stage">
    <section class="card card--front" aria-label="Card front">
      <div class="brand">
        <span class="brand__dot"></span>
        <span class="brand__name">Vantiqo</span>
      </div>
    </section>

    <section class="card card--back" aria-label="Card back">
      <div class="brand">
        <span class="brand__dot"></span>
        <span class="brand__name">Vantiqo</span>
      </div>

      <div class="divider"></div>

      <div class="contact">
        <p class="contact__name">Daniel Reeves</p>
        <p class="contact__role">Director</p>
        <p class="contact__address">1458 Harbor Lane<br>Lakeview, FL 32190</p>
        <ul class="contact__list">
          <li class="contact__item">
            <svg class="contact__icon" viewBox="0 0 14 14" fill="none" stroke="#6b2f9e" stroke-width="1.3"><rect x="3.5" y="1" width="7" height="12" rx="1.2"/><line x1="6" y1="11" x2="8" y2="11"/></svg>
            (555) 014-2290
          </li>
          <li class="contact__item">
            <svg class="contact__icon" viewBox="0 0 14 14" fill="#6b2f9e"><path d="M3 1.5l2 .3 1 3-1.4 1.2a7 7 0 0 0 3.4 3.4L9.2 8l3 1 .3 2-1.5 1.5C6 12.5 1.5 8 1.5 3z"/></svg>
            (555) 016-7731
          </li>
          <li class="contact__item">
            <svg class="contact__icon" viewBox="0 0 14 14" fill="none" stroke="#6b2f9e" stroke-width="1.3"><rect x="1" y="3" width="12" height="8" rx="1"/><path d="M1.5 3.5L7 8l5.5-4.5"/></svg>
            info@vantiqo.com
          </li>
          <li class="contact__item">
            <svg class="contact__icon" viewBox="0 0 14 14" fill="none" stroke="#6b2f9e" stroke-width="1.1"><circle cx="7" cy="7" r="5.8"/><ellipse cx="7" cy="7" rx="2.6" ry="5.8"/><line x1="1.2" y1="7" x2="12.8" y2="7"/></svg>
            www.vantiqo.com
          </li>
        </ul>
      </div>
    </section>
  </main>
</body>
</html>
```